Business card for medical clinic

I need an upmarket, modern medical/health business card for my clinic

Contact Information for Business Card

name, address, email, qr code

```html
<!DOCTYPE html>
<html lang="en">
<head>
<meta charset="utf-8">
<title>Meridian Care Partners – Business Card</title>
<link href="https://fonts.googleapis.com/css2?family=Montserrat:wght@400;500;600;700&display=swap" rel="stylesheet">
<style>
  :root {
    --backdrop: #e8e5e0;
    --card-white: #ffffff;
    --ink: #1b1b1b;
    --name-blue: #2a79ab;
    --brand-navy: #1f4a73;
    --icon-blue: #2f9ad6;
    --back-light: #0a8cc4;
    --back-dark: #03506e;
    --back-text: #ffffff;
  }
  * { margin: 0; padding: 0; box-sizing: border-box; }
  html, body {
    width: 900px;
    height: 1200px;
    overflow: hidden;
    background: var(--backdrop);
    font-family: "Montserrat", sans-serif;
  }
  .canvas {
    position: relative;
    width: 900px;
    height: 1200px;
  }
  .card {
    position: absolute;
    border-radius: 24px;
    overflow: hidden;
  }
  .card-front {
    left: 80px;
    top: 130px;
    width: 742px;
    height: 442px;
    background: var(--card-white);
    color: var(--ink);
  }
  .card-back {
    left: 78px;
    top: 638px;
    width: 744px;
    height: 440px;
    background: linear-gradient(35deg, var(--back-light) 0%, #04719a 45%, var(--back-dark) 100%);
    display: flex;
    align-items: center;
    justify-content: center;
  }
  .brand-name {
    font-family: "Montserrat", sans-serif;
    font-weight: 600;
    letter-spacing: 0.04em;
    text-transform: uppercase;
  }
  .card-front .brand-name {
    position: absolute;
    left: 30px;
    top: 72px;
    font-size: 19px;
    color: var(--brand-navy);
  }
  .card-back .brand-name {
    font-size: 36px;
    color: var(--back-text);
    letter-spacing: 0.06em;
  }
  .person {
    position: absolute;
    right: 62px;
    top: 50px;
    text-align: right;
  }
  .person-name {
    font-size: 25px;
    font-weight: 600;
    color: var(--name-blue);
    line-height: 1.2;
  }
  .person-title {
    font-size: 15px;
    font-weight: 500;
    margin-top: 3px;
  }
  .address {
    position: absolute;
    left: 46px;
    top: 248px;
    font-size: 16px;
    line-height: 21px;
  }
  .contact-list {
    position: absolute;
    left: 48px;
    top: 314px;
    list-style: none;
    font-size: 15.5px;
  }
  .contact-list li {
    display: flex;
    align-items: center;
    height: 31px;
  }
  .contact-list svg {
    width: 16px;
    height: 16px;
    margin-right: 11px;
    fill: var(--icon-blue);
    flex-shrink: 0;
  }
</style>
</head>
<body>
<main class="canvas">
  <section class="card card-front" aria-label="Card front">
    <div class="brand-name">Meridian Care Partners</div>

    <div class="person">
      <div class="person-name">Daniel Harper</div>
      <div class="person-title">Managing Director</div>
    </div>

    <address class="address" style="font-style:normal">
      240 Cedar Ridge Road<br>
      Clinton, MS 39056
    </address>

    <ul class="contact-list">
      <li>
        <svg viewBox="0 0 24 24" aria-hidden="true"><path d="M6.6 10.8a15.1 15.1 0 0 0 6.6 6.6l2.2-2.2a1 1 0 0 1 1-.25 11.4 11.4 0 0 0 3.6.57 1 1 0 0 1 1 1V20a1 1 0 0 1-1 1A17 17 0 0 1 3 4a1 1 0 0 1 1-1h3.5a1 1 0 0 1 1 1c0 1.25.2 2.45.57 3.57a1 1 0 0 1-.25 1z"/></svg>
        555.201.4470
      </li>
      <li>
        <svg viewBox="0 0 24 24" aria-hidden="true"><path d="M2 5h20v14H2z M2 5l10 7 10-7" /><path d="M3 6.5l9 6.3 9-6.3V18H3z" fill="#fff"/></svg>
        info@meridiancare.com
      </li>
      <li>
        <svg viewBox="0 0 24 24" aria-hidden="true"><circle cx="12" cy="12" r="10"/><path d="M2 12h20M12 2c3 3 3 17 0 20M12 2c-3 3-3 17 0 20" stroke="#fff" stroke-width="1.4" fill="none"/></svg>
        www.meridiancare.com
      </li>
    </ul>
  </section>

  <section class="card card-back" aria-label="Card back">
    <div class="brand-name">Meridian Care Partners</div>
  </section>
</main>
</body>
</html>
```